Website Design - TallyPorchHelpers.net

PLEASE CHECK WORD DOCUMENT ATTACHED FOR WEBSITE FLOW.

Target Market(s)

REAL ESTATE AGENTS ARE THE TARGET MARKET

Industry/Entity Type

Real Estate

Coding

Coded - Design and coding required

Number of Pages Required

4 page

Colors

Designer to choose colors to be used in the design.

Requirements
Must have
• WE LIKE RED LOGO ATTACHED
Nice to have
• PLEASE CHECK WORD DOCUMENT ATTACHED FOR WEBSITE FLOW.
Should not have

```html
<!DOCTYPE html>
<html lang="en">
<head>
<meta charset="utf-8">
<title>TallyPorchHelpers.net — Open House Sign Services</title>
<link rel="stylesheet" href="https://fonts.googleapis.com/css2?family=Poppins:wght@400;500;600;700&family=Open+Sans:wght@400;600;700&display=swap">
<style>
:root{
  --red:#e3161b;
  --red-dark:#c10f14;
  --ink:#222222;
  --text:#555555;
  --muted:#888888;
  --line:#dddddd;
  --soft:#f2f2f2;
  --blue-a:#1d5fc4;
  --blue-b:#22a3e0;
  --footer:#0b0b0b;
  --white:#ffffff;
}
*{box-sizing:border-box;margin:0;padding:0}
html,body{width:1200px;height:5099px;overflow:hidden}
body{font-family:"Open Sans",Arial,sans-serif;color:var(--text);background:var(--white);font-size:14px;line-height:1.6}
h1,h2,h3,h4,.heading{font-family:"Poppins",Arial,sans-serif;color:var(--ink)}
.section{position:relative;width:1200px;overflow:hidden}
.section-title{text-align:center;font-size:32px;font-weight:600;letter-spacing:1px;line-height:1.3;text-transform:uppercase}
.btn-outline,.btn-solid{display:inline-flex;align-items:center;justify-content:center;text-align:center;font-family:"Poppins",Arial,sans-serif;font-size:13px;font-weight:600;text-transform:uppercase;line-height:1.3;border:2px solid var(--red)}
.btn-outline{color:var(--red);background:var(--white)}
.btn-solid{color:var(--white);background:var(--red)}

/* Header */
.site-header{height:120px;display:flex;align-items:center;padding:0 100px;justify-content:space-between}
.brand{display:flex;align-items:center;gap:10px;font-family:"Poppins",sans-serif;font-weight:700;font-size:21px;color:var(--red)}
.brand-square{width:22px;height:22px;background:var(--red)}
.main-nav{display:flex;gap:30px;margin-left:-40px}
.main-nav a{font-family:"Poppins",sans-serif;font-size:14px;font-weight:500;color:var(--ink);text-decoration:none;text-transform:uppercase}
.call-box{font-family:"Poppins",sans-serif;color:var(--ink)}
.call-box .label{font-size:12px;font-weight:600}
.call-box .phone{display:flex;align-items:center;gap:8px;font-size:22px}

/* Hero */
.hero{height:526px;background:linear-gradient(180deg,#8a8f86 0%,#6d7565 30%,#4f6d34 62%,#5f8a2e 100%)}
.hero-tagline{position:absolute;right:90px;top:205px;width:640px;text-align:right;color:var(--white);font-family:"Poppins",sans-serif;font-size:24px;font-weight:600;line-height:1.6;text-shadow:0 1px 3px rgba(0,0,0,.5)}
.hero-pager{position:absolute;left:0;right:0;bottom:30px;display:flex;justify-content:center;align-items:center;gap:18px;color:var(--white);font-size:13px}

/* Choose */
.choose{height:494px;text-align:center;padding-top:110px}
.choose p{width:880px;margin:26px auto 0;font-size:13px;line-height:1.9}
.choose-options{display:flex;justify-content:center;gap:30px;margin-top:40px}
.choose-options span{width:170px;height:60px}

/* How it works */
.how{height:520px;background:var(--soft);padding-top:86px}
.how .sub{text-align:center;font-size:14px;color:var(--muted)}
.steps{position:relative;height:360px}
.step{position:absolute;width:300px;text-align:center}
.step-icon{position:relative;width:100px;height:100px;margin:0 auto;border:2px solid #bbb;border-radius:50%;background:var(--white);display:flex;align-items:center;justify-content:center}
.step-num{position:absolute;top:-10px;left:30px;width:30px;height:30px;border-radius:50%;background:var(--red);color:var(--white);font-size:13px;font-weight:700;display:flex;align-items:center;justify-content:center;border:3px solid var(--white)}
.step h3{font-size:20px;font-weight:600;margin-top:14px}
.step p{font-size:13px;margin-top:6px}

/* Services */
.services{height:625px;padding-top:90px}
.service-grid{display:flex;justify-content:center;gap:26px;margin-top:40px}
.service-card{width:232px;height:370px;border:1px solid var(--line);text-align:center}
.service-img{height:204px}
.service-card h3{font-size:20px;font-weight:600;margin-top:16px}
.service-card p{font-size:13px;padding:4px 20px 0;line-height:1.6}
.service-card .more{display:block;color:var(--red);font-weight:700;font-size:12px;margin-top:10px}
.slide-arrow{position:absolute;top:310px;color:#999;font-size:20px}

/* Pricing */
.pricing{height:870px;background:linear-gradient(120deg,var(--blue-a) 0%,#2688d6 55%,var(--blue-b) 100%);padding-top:84px;text-align:center}
.pricing .section-title{color:var(--white)}
.pricing .lead{width:640px;margin:12px auto 0;color:var(--white);font-size:14px;font-weight:600;line-height:1.6}
.plans{display:flex;justify-content:center;align-items:flex-start;margin-top:54px}
.plan{width:242px;height:465px;background:var(--white);padding-top:22px}
.plan h3{font-size:28px;font-weight:600;line-height:1.2}
.plan .tier{font-size:12px}
.price{width:80px;height:80px;border-radius:50%;background:var(--red);color:var(--white);margin:30px auto 26px;display:flex;align-items:center;justify-content:center;font-family:"Poppins",sans-serif;font-size:30px;font-weight:600;box-shadow:0 0 0 5px #f7c9ca}
.features{list-style:none;text-align:left;padding:0 26px 0 30px}
.features li{position:relative;padding-left:18px;font-size:11px;line-height:1.7;margin-bottom:12px}
.features li::before{content:"";position:absolute;left:0;top:4px;width:8px;height:4px;border-left:2px solid var(--ink);border-bottom:2px solid var(--ink);transform:rotate(-45deg)}
.plan .btn-outline{width:90px;height:34px;font-size:11px;margin-top:8px}
.plan-featured{width:256px;height:510px;margin-top:-32px;padding-top:0;box-shadow:0 8px 24px rgba(0,0,0,.25)}
.plan-featured .plan-head{background:var(--red);color:var(--white);height:96px;padding-top:22px}
.plan-featured .plan-head h3,.plan-featured .plan-head .tier{color:var(--white)}
.plan-featured .price{width:96px;height:96px;background:var(--white);color:var(--red);border:2px solid var(--line);box-shadow:none;font-size:36px}
.plan-featured .features li{font-size:13px}
.plan-featured .btn-solid{width:110px;height:40px}

/* FAQ */
.faq{height:558px;padding-top:88px}
.faq-cols{display:flex;justify-content:center;gap:60px;margin-top:22px}
.faq-col{width:480px}
.faq-item{border-bottom:1px solid var(--line);padding:14px 0 12px;display:flex;gap:14px;font-family:"Poppins",sans-serif;font-size:16px;color:var(--ink)}
.faq-item .mark{width:14px;color:var(--ink);flex:none}
.faq-item.open strong{font-weight:600;font-size:18px}
.faq-item.open p{font-family:"Open Sans",sans-serif;font-size:13px;color:var(--text);margin-top:6px}

/* Signup */
.signup{height:632px;background:var(--soft);padding-top:90px}
.channels{display:flex;justify-content:center;gap:36px;margin-top:58px}
.channel{width:220px;text-align:center}
.channel-icon{width:150px;height:150px;border-radius:50%;background:var(--white);border:2px solid #e2e2e2;margin:0 auto;display:flex;align-items:center;justify-content:center}
.channel h3{font-size:20px;font-weight:500;margin-top:22px}
.channel p{font-size:13px;line-height:1.7;margin-top:4px}

/* Clients */
.clients{height:391px;padding-top:70px}
.testimonial{display:flex;gap:40px;width:1000px;margin:32px auto 0}
.client-photo{width:160px;height:160px;border-radius:50%;flex:none;background:radial-gradient(circle at 50% 40%,#c9c4bd 0%,#8a8d92 70%,#5d6168 100%)}
.quote{font-size:13px;line-height:1.9;position:relative;padding-top:4px}
.quote .q{color:var(--red);font-family:"Poppins",sans-serif;font-weight:700;font-size:26px;line-height:0;vertical-align:-8px;margin:0 6px}
.client-name{font-family:"Poppins",sans-serif;font-weight:600;font-size:13px;color:var(--ink);margin-top:14px}
.stars{color:#f5a623;font-size:16px;letter-spacing:2px}

/* Footer */
.site-footer{height:363px;background:var(--footer);color:#cfcfcf;padding:60px 100px 0}
.footer-cols{display:flex;gap:50px}
.footer-cols h4{color:var(--white);font-size:14px;font-weight:600;text-transform:uppercase;margin-bottom:12px}
.footer-cols p,.footer-cols li{font-size:13px;line-height:1.9}
.footer-cols ul{list-style:none}
.footer-cols li::before{content:"›";color:var(--red);margin-right:8px}
.socials{display:flex;gap:12px}
.socials span{width:16px;height:16px;border-radius:50%;background:var(--white)}
.copyright{position:absolute;left:0;right:0;bottom:30px;text-align:center;font-size:12px;border-top:1px solid #333;margin:0 100px;padding-top:18px}
</style>
</head>
<body>

<header class="section site-header">
  <div class="brand"><span class="brand-square"></span>TallyPorchHelpers.net</div>
  <nav class="main-nav">
    <a href="#">Home</a><a href="#">How it works</a><a href="#">Services</a><a href="#">Pricing</a><a href="#">About us</a><a href="#">FAQ</a>
  </nav>
  <div class="call-box">
    <div class="label">CALL OR TEXT US</div>
    <div class="phone">
      <svg width="20" height="20" viewBox="0 0 24 24"><path fill="#222" d="M6.6 10.8a15 15 0 006.6 6.6l2.2-2.2a1 1 0 011-.25 11.4 11.4 0 003.6.6 1 1 0 011 1V20a1 1 0 01-1 1A17 17 0 013 4a1 1 0 011-1h3.5a1 1 0 011 1c0 1.25.2 2.45.6 3.6a1 1 0 01-.25 1z"/></svg>
      1-555-204-7318
    </div>
  </div>
</header>

<section class="section hero" role="img" aria-label="Photo of a red open house sign on a green front lawn before a suburban home">
  <p class="hero-tagline">Helping agents save time and money. We place signs and boost foot traffic to your open houses using proven marketing techniques.</p>
  <div class="hero-pager"><span>&#8592;</span><span>1 of 4</span><span>&#8594;</span></div>
</section>

<section class="section choose">
  <h2 class="section-title">Choose the option below that<br>best describes you</h2>
  <p>Lorem ipsum dolor sit amet, consectetur adipiscing elit, sed do eiusmod tempor incididunt ut labore et dolore magna aliqua. Ut enim ad minim veniam, quis nostrud exercitation ullamco laboris nisi irure dolor in reprehenderit in valur.</p>
  <div class="choose-options">
    <span class="btn-outline">I'm a full<br>on brokerage</span>
    <span class="btn-solid">I'm an ind<br>broker with a team</span>
    <span class="btn-outline">I need sign<br>placement asap</span>
  </div>
</section>

<section class="section how">
  <h2 class="section-title">How it works</h2>
  <p class="sub">3 Simple Steps of what we will do</p>
  <div class="steps">
    <svg width="1200" height="360" style="position:absolute;left:0;top:0" aria-hidden="true">
      <path d="M345 100 Q420 70 480 120" fill="none" stroke="#e3161b" stroke-width="2"/>
      <path d="M480 120 l-12 -2 l6 -10" fill="none" stroke="#e3161b" stroke-width="2"/>
      <path d="M705 120 Q780 70 850 100" fill="none" stroke="#e3161b" stroke-width="2"/>
      <path d="M850 100 l-12 -6 l10 -8" fill="none" stroke="#e3161b" stroke-width="2"/>
    </svg>
    <div class="step" style="left:110px;top:42px">
      <div class="step-icon"><span class="step-num">1</span>
        <svg width="34" height="34" viewBox="0 0 24 24"><circle cx="12" cy="8" r="4" fill="#333"/><path d="M4 21c0-4.5 3.6-7 8-7s8 2.5 8 7z" fill="#333"/></svg></div>
      <h3>Place signs strategically</h3>
      <p>Lorem Ipsum is simply dummy text of the<br>printing and typesetting industry.</p>
    </div>
    <div class="step" style="left:450px;top:112px">
      <div class="step-icon"><span class="step-num">2</span>
        <svg width="38" height="34" viewBox="0 0 24 22"><path d="M2 8h20l-3 12H5z" fill="none" stroke="#333" stroke-width="2"/><path d="M7 8l4-6M17 8l-4-6M8 12v5M12 12v5M16 12v5" stroke="#333" stroke-width="2"/></svg></div>
      <h3>Pick Up the signs</h3>
      <p>Lorem Ipsum is simply dummy text of the<br>printing and typesetting industry.</p>
    </div>
    <div class="step" style="left:790px;top:42px">
      <div class="step-icon"><span class="step-num">3</span>
        <svg width="38" height="30" viewBox="0 0 26 20"><rect x="1" y="3" width="15" height="11" fill="#333"/><path d="M16 7h5l4 4v3h-9z" fill="#333"/><circle cx="6" cy="16" r="2.5" fill="#333"/><circle cx="20" cy="16" r="2.5" fill="#333"/></svg></div>
      <h3>Store Custom Signs</h3>
      <p>Lorem Ipsum is simply dummy text of the<br>printing and typesetting industry.</p>
    </div>
  </div>
</section>

<section class="section services">
  <h2 class="section-title">Our Services</h2>
  <span class="slide-arrow" style="left:40px">&#8249;</span>
  <span class="slide-arrow" style="right:40px">&#8250;</span>
  <div class="service-grid">
    <article class="service-card">
      <div class="service-img" role="img" aria-label="Photo of an open house sign on a lawn" style="background:linear-gradient(180deg,#9a8f7e,#6f8a45)"></div>
      <h3>Sales</h3><p>Lorem Ipsum is simply dummy text of the printing industry.</p><span class="more">READ MORE</span>
    </article>
    <article class="service-card">
      <div class="service-img" role="img" aria-label="Photo of an open house sign being installed" style="background:linear-gradient(180deg,#b9b3a6,#5f7f3b)"></div>
      <h3>Install</h3><p>Lorem Ipsum is simply dummy text of the printing industry.</p><span class="more">READ MORE</span>
    </article>
    <article class="service-card">
      <div class="service-img" role="img" aria-label="Photo of a red open house sign on a street corner" style="background:linear-gradient(180deg,#c9c1b6,#b8262a 55%,#6d7a4a)"></div>
      <h3>Maintanance</h3><p>Lorem Ipsum is simply dummy text of the printing industry.</p><span class="more">READ MORE</span>
    </article>
    <article class="service-card">
      <div class="service-img" role="img" aria-label="Photo of an open house sign in front of a brick home" style="background:linear-gradient(180deg,#a9c1d8,#8a5a44 50%,#6d8a45)"></div>
      <h3>Store Signs</h3><p>Lorem Ipsum is simply dummy text of the printing industry.</p><span class="more">READ MORE</span>
    </article>
  </div>
</section>

<section class="section pricing">
  <h2 class="section-title">Pricing</h2>
  <p class="lead">Lorem Ipsum is simply dummy text of the printing and typesetting industry. Lorem Ipsum has been the industry's standard dummy text ever since the 1500.</p>
  <span class="slide-arrow" style="left:60px;top:410px;color:#fff">&#8249;</span>
  <span class="slide-arrow" style="right:60px;top:410px;color:#fff">&#8250;</span>
  <div class="plans">
    <div class="plan">
      <h3>5 SIGNS</h3><div class="tier">Lorem Ipsum</div>
      <div class="price">$49</div>
      <ul class="features">
        <li>Place signs strategically in best areas according to where the open house is located</li>
        <li>Pick Up the signs after the open house</li>
        <li>Store custom signs for you if needed</li>
      </ul>
      <span class="btn-outline">Buy now</span>
    </div>
    <div class="plan plan-featured">
      <div class="plan-head"><h3>10 SIGNS</h3><div class="tier">Lorem Ipsum</div></div>
      <div class="price">$59</div>
      <ul class="features">
        <li>Place signs strategically in best areas according to where the open house is located</li>
        <li>Pick Up the signs after the open house</li>
        <li>Store custom signs for you if needed</li>
      </ul>
      <span class="btn-solid">Buy now</span>
    </div>
    <div class="plan">
      <h3>15 SIGNS</h3><div class="tier">Lorem Ipsum</div>
      <div class="price">$69</div>
      <ul class="features">
        <li>Place signs strategically in best areas according to where the open house is located</li>
        <li>Pick Up the signs after the open house</li>
        <li>Store custom signs for you if needed</li>
      </ul>
      <span class="btn-outline">Buy now</span>
    </div>
  </div>
</section>

<section class="section faq">
  <h2 class="section-title">FAQ</h2>
  <div class="faq-cols">
    <div class="faq-col">
      <div class="faq-item open"><span class="mark">&#8211;</span><div><strong>Lorem Ipsum Is Simply Dummy Text?</strong><p>Sed ut perspiciatis unde omnis iste natus error sit voluptatem ac cusan tium doloremque laudantium, totam aim dolores.</p></div></div>
      <div class="faq-item"><span class="mark">+</span>Lorem Ipsum Is Simply Dummy?</div>
      <div class="faq-item"><span class="mark">+</span>Nemo enim ipsam voluptatem voluptas?</div>
      <div class="faq-item"><span class="mark">+</span>Lorem Ipsum Is Simply Dummy Since 1500?</div>
    </div>
    <div class="faq-col">
      <div class="faq-item"><span class="mark">+</span>Lorem Ipsum Is Simply Dummy Text?</div>
      <div class="faq-item"><span class="mark">+</span>Quis autem vel eum iure reprehenderin?</div>
      <div class="faq-item"><span class="mark">+</span>Lorem Ipsum Is Simply Dummy?</div>
      <div class="faq-item"><span class="mark">+</span>Nemo enim ipsam voluptatem voluptas?</div>
      <div class="faq-item"><span class="mark">+</span>Lorem Ipsum Is Simply Dummy Since 1500?</div>
    </div>
  </div>
</section>

<section class="section signup">
  <h2 class="section-title">Sign up for a subscription and get these<br>marketing services for free</h2>
  <div class="channels">
    <div class="channel">
      <div class="channel-icon"><svg width="62" height="56" viewBox="0 0 62 56"><path d="M4 4h54v36H24l-12 12V40H4z" fill="none" stroke="#e3161b" stroke-width="3"/><text x="31" y="28" text-anchor="middle" font-family="Poppins,sans-serif" font-size="14" font-weight="600" fill="#e3161b">SMS</text></svg></div>
      <h3>SMS</h3><p>Send sms blast to your neighborhood informing them your home is for sale and if they know anyone looking to send them over</p>
    </div>
    <div class="channel">
      <div class="channel-icon"><svg width="64" height="44" viewBox="0 0 64 44"><rect x="2" y="2" width="60" height="40" fill="none" stroke="#e3161b" stroke-width="3"/><path d="M2 2l30 22 30-22M2 42l22-18M62 42L40 24" fill="none" stroke="#e3161b" stroke-width="3"/></svg></div>
      <h3>EMAIL</h3><p>Email blast to your neighborhood informing them your home is for sale and if they know anyone looking to send them over</p>
    </div>
    <div class="channel">
      <div class="channel-icon"><span style="width:50px;height:50px;background:var(--red);display:block"></span></div>
      <h3>FB AD</h3><p>Newsfeed ads to people in your open house area</p>
    </div>
    <div class="channel">
      <div class="channel-icon"><span style="width:50px;height:50px;border-radius:50%;background:var(--red);display:block"></span></div>
      <h3>VB</h3><p>VB blast to your neighborhood informing them your home is for sale and if they know anyone looking to send them over</p>
    </div>
  </div>
</section>

<section class="section clients">
  <h2 class="section-title">Happy Clients</h2>
  <div class="testimonial">
    <div class="client-photo" role="img" aria-label="Portrait photo of a satisfied client"></div>
    <div>
      <p class="quote"><span class="q">&#8220;</span>Aliquam dictum elit vitae mauris facilisis, at dictum urna dignissim. Donec sed lectus vel felis lacinia luctus vitae nisi iaculis arcu. Mauris mattis, massa eu porta ultricies. Aliquam dictum elit vitae nisl pulvinar at varius velit posuere. Nam ante dui dignissim ac porta aucto facilisis, at dictum urna dignissim.<span class="q">&#8221;</span></p>
      <div class="client-name">MARCUS DELANE, HAPPY CLIENT</div>
      <div class="stars">&#9733;&#9733;&#9733;&#9733;&#9733;</div>
    </div>
  </div>
</section>

<footer class="section site-footer">
  <div class="footer-cols">
    <div style="width:230px"><h4>About us</h4><p>Helping agents leverage their time and skills to increase production at an affordable price with impeccable support.</p></div>
    <div style="width:140px"><h4>Quick links</h4><ul><li>Home</li><li>How It Works</li><li>Service Areas</li><li>Pricing</li><li>About Us</li><li>FAQ</li></ul></div>
    <div style="width:230px"><h4>Contact</h4><p>TallyPorch Helpers,<br>1610 S. Lorem Ipsum Is Simple,<br>Lorem Ipsum.</p><p>(+1) 555-014-2290</p><p>info@tallyporchhelpers.net</p></div>
    <div style="width:140px"><h4>Other links</h4><ul><li>Latest Work</li><li>Blog</li><li>Contact Us</li></ul></div>
    <div><h4>Follow us on</h4><div class="socials"><span></span><span></span><span></span></div></div>
  </div>
  <div class="copyright">Copyright &copy; 2018 . All Rights Reserved.</div>
</footer>

</body>
</html>
```